Buch-/eBook-Cover für Sachbuch gesucht
Zielgruppe
We're selfpublishing nonfiction books. Interested are adults - mostly man (age range: 25-50) - who want to learn more about leadership at their workplaces.
Aufgabenstellung
The design should be clean and simple, title easy to read, good color contrast (the cover has to stand out from an white background).

```html
<!DOCTYPE html>
<html lang="en">
<head>
<meta charset="utf-8">
<title>Leadership – Book Cover</title>
<link rel="stylesheet" href="https://fonts.googleapis.com/css2?family=Caveat+Brush&family=Roboto+Condensed:wght@700&display=swap">
<style>
  :root {
    --page-bg: #ebebeb;
    --cover-dark: #0c111b;
    --cover-navy: #0f1e3d;
    --streak-blue: #1b5cab;
    --streak-deep: #14407e;
    --text-light: #f4f4f2;
  }
  html, body {
    margin: 0;
    padding: 0;
    width: 1200px;
    height: 1200px;
    overflow: hidden;
    background: var(--page-bg);
  }
  .canvas {
    position: relative;
    width: 1200px;
    height: 1200px;
  }
  .book-cover {
    position: absolute;
    left: 210px;
    top: 50px;
    width: 780px;
    height: 1100px;
    overflow: hidden;
    background: var(--cover-dark);
  }
  .cover-art {
    position: absolute;
    inset: 0;
    background:
      radial-gradient(ellipse 260px 60px at 230px 20px, rgba(27,92,171,0.55), transparent 70%),
      linear-gradient(155deg, transparent 36%, rgba(27,92,171,0.45) 44%, transparent 52%),
      linear-gradient(150deg, transparent 52%, rgba(20,64,126,0.55) 58%, rgba(27,92,171,0.7) 62%, transparent 70%),
      linear-gradient(152deg, transparent 68%, rgba(27,92,171,0.5) 76%, transparent 84%),
      linear-gradient(160deg, var(--cover-navy) 0%, var(--cover-dark) 40%, var(--cover-navy) 70%, var(--cover-dark) 100%);
  }
  .spine-edge {
    position: absolute;
    left: 0;
    top: 0;
    width: 40px;
    height: 100%;
    background: linear-gradient(90deg, rgba(255,255,255,0.04), rgba(0,0,0,0.25) 85%, rgba(255,255,255,0.05));
  }
  .title {
    position: absolute;
    left: 0;
    right: 0;
    top: 205px;
    margin: 0;
    text-align: center;
    font-family: "Caveat Brush", cursive;
    font-weight: 400;
    font-size: 168px;
    line-height: 1;
    color: var(--text-light);
    letter-spacing: 1px;
    padding-left: 50px;
  }
  .subtitle {
    position: absolute;
    left: 0;
    right: 0;
    top: 400px;
    margin: 0;
    text-align: center;
    font-family: "Roboto Condensed", sans-serif;
    font-weight: 700;
    font-size: 44px;
    line-height: 55px;
    color: var(--text-light);
    text-transform: uppercase;
    padding-left: 20px;
  }
  .author {
    position: absolute;
    left: 0;
    right: 0;
    top: 1015px;
    margin: 0;
    text-align: center;
    font-family: "Roboto Condensed", sans-serif;
    font-weight: 700;
    font-size: 30px;
    color: var(--text-light);
    text-transform: uppercase;
    padding-left: 20px;
  }
</style>
</head>
<body>
  <div class="canvas">
    <div class="book-cover">
      <div class="cover-art" role="img" aria-label="Abstract dark navy background with soft diagonal streaks of blue light"></div>
      <div class="spine-edge"></div>
      <h1 class="title">Leadership</h1>
      <p class="subtitle">Fostering Growth<br>and Inspiring Excellence</p>
      <p class="author">Daniel Harwick</p>
    </div>
  </div>
</body>
</html>
```